Letter design, envelope design, and more

Hello, we the Tavrin Gmbh are looking for our shop. Letter C5. Design does not have to be like a business card, so it can have straight lines. Only the color is important. The logo is the text under TaVRin omit.It should not be playful but Profesionel

Font styles to use
Sans Serif

Colors
0555a3
3176b5
85abd2
85cae6
34a7d8
0792cd
cee9f5
cfdfed
000000

Requirements
Must have
• Color like business card, Please, with the text under TaVRin, Correct address Lindmattstr. 4 Zip code 9517 Goldach, as well as Couvert Without addressing only design and logo with TaVrn
Nice to have
• more writing articles
Should not have
• Not too colored, Text under TaVRin, bright colors

```html
<!DOCTYPE html>
<html lang="en">
<head>
<meta charset="utf-8">
<title>Tavrin Gmbh – Stationery</title>
<link rel="stylesheet" href="https://fonts.googleapis.com/css2?family=Questrial&family=Roboto:wght@400&display=swap">
<style>
  :root {
    --backdrop: #dcdcdc;
    --paper: #f7f7f7;
    --brand-blue: #0555a3;
    --brand-blue-mid: #3176b5;
    --brand-blue-soft: #85abd2;
    --brand-blue-pale: #cfdfed;
    --ink: #4a4d55;
    --ink-soft: #5c5f66;
  }
  * { margin: 0; padding: 0; box-sizing: border-box; }
  html, body { width: 1200px; height: 877px; overflow: hidden; }
  body {
    position: relative;
    background: var(--backdrop);
    font-family: "Questrial", sans-serif;
    color: var(--ink);
  }
  .brand-name {
    font-family: "Questrial", sans-serif;
    color: var(--brand-blue);
    letter-spacing: 0.06em;
    white-space: nowrap;
    display: flex;
    align-items: center;
    gap: 8px;
  }
  .brand-name .mark {
    width: 16px; height: 16px;
    background: var(--brand-blue);
    display: inline-block;
  }

  /* Letterhead */
  .letterhead {
    position: absolute; left: 69px; top: 64px;
    width: 527px; height: 742px;
    background: var(--paper);
  }
  .letterhead .brand-name {
    position: absolute; left: 0; right: 0; top: 52px;
    justify-content: center; font-size: 27px;
  }
  .salutation {
    position: absolute; left: 45px; top: 207px;
    font-size: 14px; color: var(--ink-soft);
  }
  .letter-body {
    position: absolute; left: 45px; top: 248px; width: 440px;
    font-size: 7.55px; line-height: 11.3px; text-align: justify;
  }
  .letter-body p { margin-bottom: 11.3px; }
  .closing {
    position: absolute; left: 45px; top: 487px; font-size: 7.6px;
  }
  .signature {
    position: absolute; left: 41px; top: 520px;
    width: 94px; height: 40px;
    background: var(--brand-blue-pale);
    border-radius: 3px;
  }
  .contact-list {
    position: absolute; left: 25px; top: 674px;
    list-style: none; font-family: "Roboto", sans-serif;
    font-size: 7.9px; line-height: 10.4px; color: var(--ink);
  }
  .contact-list li { display: flex; align-items: center; gap: 4px; }
  .contact-list svg { width: 7px; height: 7px; fill: var(--brand-blue); }
  .letter-address {
    position: absolute; right: 27px; top: 679px;
    font-family: "Roboto", sans-serif;
    font-size: 7.9px; line-height: 9.8px; text-align: right;
  }
  .footer-rule {
    position: absolute; left: 94px; right: 27px; top: 702px;
    height: 1px; background: var(--brand-blue-mid);
  }

  /* Envelopes */
  .envelope {
    position: absolute; width: 532px; height: 242px;
    background: var(--paper);
  }
  .envelope-back { left: 614px; top: 268px; }
  .envelope-front { left: 614px; top: 562px; }
  .flap { position: absolute; left: 0; top: 0; width: 532px; height: 74px; }
  .flap path { fill: var(--brand-blue); }
  .flap-name {
    position: absolute; left: 0; right: 0; top: 24px;
    text-align: center; font-size: 22px; letter-spacing: 0.06em;
    color: #ffffff;
  }
  .envelope-front .brand-name {
    position: absolute; left: 27px; top: 28px; font-size: 21px;
  }
  .envelope-front .brand-name .mark { width: 14px; height: 14px; }
  .sender-line {
    position: absolute; left: 27px; top: 67px;
    font-family: "Roboto", sans-serif; font-size: 7.9px; color: var(--ink);
  }
</style>
</head>
<body>

<section class="letterhead">
  <div class="brand-name"><span class="mark"></span>TAVRIN GMBH</div>

  <p class="salutation">Dear Mr. Keller,</p>

  <div class="letter-body">
    <p>Lorem ipsum dolor sit amet, consectetur adipiscing elit. Donec orci purus, luctus vitae dignissim eu, iaculis sed purus. Vivamus faucibus, ipsum nec aliquet viverra, leo mauris condimentum ligula, sit amet sagittis enim ligula quis arcu. Nam egestas tortor id nisi porttitor mattis. In tortor ante, ultricies in suscipit a, tempus non massa. Vivamus et auctor mi. Fusce vel massa nulla. Phasellus nec eros mauris, et scelerisque orci.</p>
    <p>Donec malesuada orci vitae nulla accumsan porta a id massa. Quisque accumsan iaculis magna sit amet fringilla. Maecenas consequat, magna eget tincidunt semper, odio nibh rutrum mi, id feugiat ante nisi eu risus. Vestibulum nunc orci, rhoncus a placerat in, ultricies in mi. Cras mattis varius eros, vel fringilla nisi suscipit eget. Quisque scelerisque sagittis nulla at porttitor.</p>
    <p>Sed id augue vitae urna euismod commodo aliquet a quam. Pellentesque arcu velit, cursus et malesuada ut, consequat et diam. Nullam erat sem, rhoncus id ullamcorper vitae, rhoncus et arcu. In ultricies ultricies nulla, ut rutrum nisi iaculis at. Donec eu magna a metus ornare faucibus. Fusce aliquet faucibus ultricies. Morbi semper, est id tincidunt gravida, sem arcu adipiscing lacus, ac bibendum nulla leo eu purus. Quisque nec diam sed risus consectetur a ccumsan quis quis nibh. Vestibulum id purus lorem.</p>
    <p>It is a long established fact that a reader will be distracted by the readable content of a page when looking at its layout. The point of using Lorem Ipsum is that it has a more-or-less normal distribution of letters, as opposed to using 'Content here, content here', making it look like readable English. Many desktop publishing packages</p>
  </div>

  <p class="closing">Sincerely,</p>
  <div class="signature" role="img" aria-label="Handwritten signature of the sender"></div>

  <ul class="contact-list">
    <li><svg viewBox="0 0 10 10"><path d="M2 0.5 L3.8 2.6 L2.9 3.8 Q4 6 6.2 7.1 L7.4 6.2 L9.5 8 L8.3 9.5 Q4 9.5 0.5 4.2 Q0.5 1.6 2 0.5Z"/></svg>+41 71 555 02 30</li>
    <li><svg viewBox="0 0 10 10"><path d="M0 1.5 H10 V8.5 H0Z"/><path d="M0.8 2.3 L5 5.4 L9.2 2.3" stroke="#f7f7f7" stroke-width="0.9" fill="none"/></svg>info@tavrin.ch</li>
    <li><svg viewBox="0 0 10 10"><circle cx="5" cy="5" r="5"/><path d="M0 5 H10 M5 0 Q2 5 5 10 M5 0 Q8 5 5 10" stroke="#f7f7f7" stroke-width="0.8" fill="none"/></svg>www.tavrin.ch</li>
  </ul>
  <div class="letter-address">Lindmattstr. 4<br>9517 Goldach</div>
  <div class="footer-rule"></div>
</section>

<section class="envelope envelope-back">
  <svg class="flap" viewBox="0 0 532 74" aria-hidden="true">
    <path d="M0 0 H532 L526 38 Q520 74 488 74 H44 Q12 74 7 42 Z"/>
  </svg>
  <div class="flap-name">TAVRIN</div>
</section>

<section class="envelope envelope-front">
  <div class="brand-name"><span class="mark"></span>TAVRIN GMBH</div>
  <p class="sender-line">Lindmattstr. 4, 9517 Goldach</p>
</section>

</body>
</html>
```